K7 Electrical Services Ltd Web design

I require a web site for my new electrical contracting company. We are customer service orientated. Offering high value electrical installations, design and maintenance. Focused on custom residential and commercial upgrading. Lighting design and application are paramount in our company's services. Industry leading product use and integration are always on the forefront with our customer client services. As well as energy efficiency.

Target Market(s)

Homebuilders, General Contractors, Property management companies, clients, individuals,

Industry/Entity Type

Electric Company

Coding

Coded - Design and coding required

Number of Pages Required

3 page

Requirements
Must have
• Classic, modern, edgy but not trendy . Appeals to the masse.
• 3 page
• home page
• about page
• gallery page
• ability to contact from the webiste
Nice to have
• open to all types of designs that are relative to the construction industry.
• Black, Grey, metallic ice blue and deep purple colours from the logo.
Should not have
• anything cheesy with cartoon light bulb images.

```html
<!DOCTYPE html>
<html lang="en">
<head>
<meta charset="utf-8">
<title>K7 Electrical Services Ltd</title>
<link rel="stylesheet" href="https://fonts.googleapis.com/css2?family=Montserrat:wght@400;600;700&family=PT+Sans:wght@400;700&display=swap">
<style>
:root{
  --purple:#62298f;
  --purple-deep:#5a2787;
  --purple-soft:#7a4ba8;
  --grey:#5e5e61;
  --ink:#2b2b2e;
  --text:#555559;
  --muted:#c9c9cc;
  --white:#ffffff;
}
*{box-sizing:border-box;margin:0;padding:0}
html,body{width:1200px;height:2956px;overflow:hidden}
body{position:relative;background:var(--white);font-family:"PT Sans",sans-serif;color:var(--text)}
.abs{position:absolute}
.heading{font-family:"Montserrat",sans-serif;font-weight:700;text-transform:uppercase}
.rule{position:absolute;width:46px;height:3px}
.btn{position:absolute;background:var(--purple);color:var(--white);font-family:"Montserrat",sans-serif;font-weight:600;font-size:13px;text-transform:uppercase;display:flex;align-items:center;justify-content:center;letter-spacing:.3px;text-decoration:none}

/* header */
.site-header{left:0;top:0;width:1200px;height:122px;background:var(--white)}
.brand{left:130px;top:22px;font-family:"Montserrat",sans-serif;font-weight:700;color:var(--purple);font-size:30px;line-height:34px;letter-spacing:1px}
.call{left:684px;top:22px;display:flex;align-items:center;gap:10px}
.call-icon{width:28px;height:28px;border-radius:50%;background:var(--purple);display:flex;align-items:center;justify-content:center}
.call-label{font-family:"Montserrat",sans-serif;font-size:10px;font-weight:600;color:var(--ink)}
.call-number{font-family:"Montserrat",sans-serif;font-size:22px;color:var(--purple);line-height:1}
.follow{left:893px;top:32px;display:flex;align-items:center;gap:6px;font-family:"Montserrat",sans-serif;font-size:10px;font-weight:600;color:var(--ink)}
.follow .label{margin-right:8px}
.dot{width:26px;height:26px;border-radius:50%;background:var(--purple)}
.main-nav{left:484px;top:80px;display:flex}
.main-nav a{font-family:"Montserrat",sans-serif;font-size:12px;font-weight:600;color:var(--ink);text-decoration:none;text-transform:uppercase;padding:7px 10px;margin-right:14px}
.main-nav a.active{background:var(--purple);color:var(--white)}

/* hero */
.hero{left:0;top:122px;width:1200px;height:552px;background:linear-gradient(90deg,#9bbccd 0%,#3c6b88 35%,#345d78 55%,#7f8f9a 75%,#b7c4cc 100%)}
.hero-title{left:132px;top:290px;font-family:"Montserrat",sans-serif;font-weight:600;font-size:48px;line-height:54px;color:var(--white)}
.slider-dots{left:540px;top:614px;display:flex;gap:14px;align-items:center}
.slider-dots span{width:8px;height:8px;border-radius:50%;background:rgba(255,255,255,.6)}
.slider-dots span.on{width:14px;height:14px;border:2px solid var(--white);background:transparent}

/* services */
.services{left:0;top:674px;width:1200px;height:524px;background:var(--grey)}
.section-title{left:0;width:1200px;text-align:center;font-size:21px;line-height:26px;color:var(--white)}
.service{top:848px;width:236px;text-align:center;color:var(--white)}
.service svg{display:block;margin:0 auto 26px}
.service h3{font-family:"Montserrat",sans-serif;font-weight:700;font-size:14px;line-height:18px}
.service p{margin:10px auto 0;width:200px;font-size:12px;line-height:16px;color:#cfcfd2}
.divider-v{top:840px;width:1px;height:215px;background:#7b7b7f}

/* welcome */
.welcome{left:0;top:1198px;width:1200px;height:449px;background:#f7f7f7}
.welcome-photo{left:532px;top:1198px;width:668px;height:449px;background:linear-gradient(120deg,#f4f4f4 0%,#e6dede 40%,#d3b3b8 60%,#efe9e9 100%)}
.welcome-heading{left:132px;top:1276px;font-size:21px;line-height:26px;color:var(--purple)}
.welcome-text{left:132px;top:1350px;width:350px;font-size:13px;line-height:21px;color:#444}

/* testimonials */
.testimonials{left:0;top:1647px;width:1200px;height:369px;background:var(--white)}
.cable{top:1800px;width:300px;height:170px}
.cable-left{left:40px;background:linear-gradient(200deg,#f0f0f0 0%,#dcdcdc 60%,#ffffff 100%)}
.cable-right{left:860px;background:linear-gradient(160deg,#f0f0f0 0%,#dcdcdc 60%,#ffffff 100%)}
.quote{left:380px;top:1796px;width:440px;text-align:center;font-size:13px;line-height:21px;color:#333}
.author{left:0;top:1928px;width:1200px;text-align:center;font-family:"Montserrat",sans-serif;font-weight:600;font-size:13px;color:var(--ink)}
.author small{display:block;font-size:10px;margin-top:4px}
.arrow{top:1830px}

/* blog */
.blog{left:0;top:2016px;width:1200px;height:565px;background:linear-gradient(180deg,#6a6a6d 0%,#5b5b5e 100%)}
.card{top:2159px;width:296px;height:369px;background:var(--white);box-shadow:0 4px 14px rgba(0,0,0,.25)}
.card-photo{width:296px;height:193px}
.card h4{margin:24px 24px 0;font-family:"Montserrat",sans-serif;font-weight:700;font-size:16px;color:var(--ink)}
.card p{margin:10px 24px 0;font-size:12.5px;line-height:17px;color:#444}
.card .btn{left:24px;top:320px;width:92px;height:28px;font-size:11px}

/* footer */
.site-footer{left:0;top:2581px;width:1200px;height:375px;background:var(--purple-deep)}
.footer-brand{left:130px;top:2652px;font-family:"Montserrat",sans-serif;font-weight:700;font-size:33px;line-height:42px;letter-spacing:1px;color:var(--white)}
.footer-col{top:2636px;color:var(--white)}
.footer-col h5{font-family:"Montserrat",sans-serif;font-weight:700;font-size:12px;margin-bottom:20px}
.footer-col ul{list-style:none;font-size:12px;line-height:18px}
.contact-list li{display:flex;gap:12px;margin-bottom:16px;align-items:flex-start}
.contact-list svg{flex:none;margin-top:3px}
.email-field{width:207px;height:39px;background:var(--white);color:#777;font-size:12px;padding:11px 16px}
.signup{margin-top:18px;width:76px;height:30px;border:2px solid var(--white);font-family:"Montserrat",sans-serif;font-size:11px;font-weight:700;display:flex;align-items:center;justify-content:center}
.footer-rule{left:130px;top:2846px;width:940px;height:1px;background:rgba(255,255,255,.25)}
.footer-follow{left:130px;top:2886px;display:flex;align-items:center;gap:6px;font-family:"Montserrat",sans-serif;font-size:12px;font-weight:700;color:var(--white)}
.footer-follow .label{margin-right:16px}
.footer-follow .dot{background:var(--purple-soft);border:1px solid rgba(255,255,255,.4)}
.copyright{left:760px;top:2892px;width:308px;text-align:right;font-size:12px;color:var(--white)}
</style>
</head>
<body>

<header class="site-header abs">
  <div class="brand abs">K7 ELECTRICAL<br>SERVICES</div>
  <div class="call abs">
    <div class="call-icon"><svg width="14" height="14" viewBox="0 0 24 24"><path fill="#fff" d="M6.6 10.8a15 15 0 0 0 6.6 6.6l2.2-2.2c.3-.3.7-.4 1-.2 1.1.4 2.3.6 3.6.6.6 0 1 .4 1 1V20c0 .6-.4 1-1 1A17 17 0 0 1 3 4c0-.6.4-1 1-1h3.5c.6 0 1 .4 1 1 0 1.3.2 2.5.6 3.6.1.3 0 .7-.2 1z"/></svg></div>
    <div><div class="call-label">CALL US NOW</div><div class="call-number">555.010.4477</div></div>
  </div>
  <div class="follow abs"><span class="label">FOLLOW US</span><span class="dot"></span><span class="dot"></span><span class="dot"></span></div>
  <nav class="main-nav abs">
    <a class="active" href="#">Home</a><a href="#">About Us</a><a href="#">Services</a><a href="#">Installations</a><a href="#">Testimonials</a><a href="#">Contact Us</a>
  </nav>
</header>

<section class="hero abs" role="img" aria-label="Photo of an electrician in a hard hat and gloves working at an industrial switch panel"></section>
<h1 class="hero-title abs">Electrical<br>Contracting</h1>
<a class="btn" href="#" style="left:140px;top:418px;width:134px;height:36px">Read More</a>
<div class="slider-dots abs"><span></span><span class="on"></span><span></span><span></span></div>

<section class="services abs"></section>
<h2 class="section-title heading abs" style="top:722px">Our Services</h2>
<div class="rule" style="left:577px;top:762px;background:var(--muted)"></div>

<div class="service abs" style="left:106px">
  <svg width="62" height="62" viewBox="0 0 62 62"><circle cx="31" cy="31" r="28" fill="none" stroke="#fff" stroke-width="3"/><rect x="22" y="22" width="18" height="14" rx="3" fill="#fff"/><rect x="25" y="14" width="3" height="9" fill="#fff"/><rect x="34" y="14" width="3" height="9" fill="#fff"/><path d="M31 36v12" stroke="#fff" stroke-width="3"/></svg>
  <h3>Electrical Installations</h3>
  <p>Donec eu felis dapibus, ullamcorper risus nec, facilisis justo. Quisque iaculis felis nec tortor molestie, eu vestibulum lorem placerat.</p>
</div>
<div class="divider-v abs" style="left:343px"></div>
<div class="service abs" style="left:348px">
  <svg width="62" height="62" viewBox="0 0 62 62"><path d="M12 50 44 18" stroke="#fff" stroke-width="6" stroke-linecap="round"/><circle cx="46" cy="16" r="8" fill="none" stroke="#fff" stroke-width="4"/><path d="M14 12 50 48" stroke="#fff" stroke-width="5" stroke-linecap="round"/></svg>
  <h3>Design and Maintenance</h3>
  <p>Donec eu felis dapibus, ullamcorper risus nec, facilisis justo. Quisque iaculis felis nec tortor molestie, eu vestibulum lorem placerat.</p>
</div>
<div class="divider-v abs" style="left:601px"></div>
<div class="service abs" style="left:601px">
  <svg width="62" height="62" viewBox="0 0 62 62"><path d="M31 6 4 30h8v26h38V30h8z" fill="#fff"/><path d="M34 26 24 40h8l-4 12 12-16h-8z" fill="#5e5e61"/></svg>
  <h3>Residential and<br>Commercial Upgrading</h3>
  <p>Donec eu felis dapibus, ullamcorper risus nec, facilisis justo. Quisque iaculis felis nec tortor molestie.</p>
</div>
<div class="divider-v abs" style="left:837px"></div>
<div class="service abs" style="left:858px">
  <svg width="62" height="62" viewBox="0 0 62 62"><circle cx="31" cy="24" r="16" fill="#fff"/><rect x="24" y="38" width="14" height="8" fill="#fff"/><rect x="25" y="48" width="12" height="4" rx="2" fill="#fff"/><path d="M27 30l4-8 4 8" stroke="#5e5e61" stroke-width="2" fill="none"/></svg>
  <h3>Lighting design and application</h3>
  <p>Donec eu felis dapibus, ullamcorper risus nec, facilisis justo. Quisque iaculis felis nec tortor molestie, eu vestibulum lorem placerat.</p>
</div>
<a class="btn" href="#" style="left:520px;top:1117px;width:160px;height:36px">View All Services</a>

<section class="welcome abs"></section>
<div class="welcome-photo abs" role="img" aria-label="Photo of an electrician in a checked shirt fitting a ceiling light from a ladder"></div>
<h2 class="heading abs welcome-heading">Welcome to our site</h2>
<div class="rule" style="left:132px;top:1316px;background:#bdbdc0"></div>
<p class="abs welcome-text">There are many variations of passages of Lorem Ipsum available, but the majority have suffered alteration in some form, by injected humour, or randomised words which don't look even slightly believable. If you are going to use a passage of Lorem Ipsum, you need to be sure there isn't anything embarrassing hidden in the middle of text.</p>
<a class="btn" href="#" style="left:136px;top:1500px;width:120px;height:35px">Read More</a>

<section class="testimonials abs"></section>
<div class="cable cable-left abs" role="img" aria-label="Photo of a stripped electrical cable with coloured wires"></div>
<div class="cable cable-right abs" role="img" aria-label="Photo of a stripped electrical cable with coloured wires"></div>
<h2 class="section-title heading abs" style="top:1701px;color:var(--purple)">Testimonials</h2>
<div class="rule" style="left:577px;top:1744px;background:#999"></div>
<svg class="arrow abs" style="left:244px" width="20" height="34" viewBox="0 0 20 34"><path d="M16 3 4 17l12 14" stroke="#c8c8c8" stroke-width="4" fill="none"/></svg>
<svg class="arrow abs" style="left:932px" width="20" height="34" viewBox="0 0 20 34"><path d="M4 3l12 14L4 31" stroke="#c8c8c8" stroke-width="4" fill="none"/></svg>
<p class="quote abs">There are many variations of passages of Lorem Ipsum available, but the majority have suffered alteration in some form, by injected humour, or randomised words which don't look even slightly believable lorem Ipsum available, butthe majority have suffered alteration in some</p>
<div class="author abs">DANIEL MORROW<small>ENGLAND</small></div>

<section class="blog abs"></section>
<h2 class="section-title heading abs" style="top:2067px">Latest Blog</h2>
<div class="rule" style="left:577px;top:2108px;background:var(--muted)"></div>

<article class="card abs" style="left:128px">
  <div class="card-photo" role="img" aria-label="Photo of an electrician in a yellow hard hat wiring a panel" style="background:linear-gradient(135deg,#c9a54a,#6b5b4a 50%,#3e3a3a)"></div>
  <h4>Lorem Ipsum is simply</h4>
  <p>There are many variations of passages of Lorem Ipsum availabl. more-or-less normal distribution of letter</p>
  <a class="btn" href="#">Read More</a>
</article>
<article class="card abs" style="left:447px">
  <div class="card-photo" role="img" aria-label="Photo of an electrician in a blue hard hat beside a switchboard" style="background:linear-gradient(135deg,#4a78b8,#9aa7b3 55%,#5f6670)"></div>
  <h4>Lorem Ipsum is simply</h4>
  <p>There are many variations of passages of Lorem Ipsum availabl. more-or-less normal distribution of letter</p>
  <a class="btn" href="#">Read More</a>
</article>
<article class="card abs" style="left:770px">
  <div class="card-photo" role="img" aria-label="Photo of an electrician in an orange hard hat at work" style="background:linear-gradient(135deg,#8fb7cf,#d19a4a 50%,#5a6e7d)"></div>
  <h4>Lorem Ipsum is simply</h4>
  <p>There are many variations of passages of Lorem Ipsum availabl. more-or-less normal distribution of letter</p>
  <a class="btn" href="#">Read More</a>
</article>

<footer class="site-footer abs"></footer>
<div class="footer-brand abs">K7 ELECTRICAL<br>SERVICES</div>
<div class="footer-col abs" style="left:481px">
  <h5>CONTACT US</h5>
  <ul class="contact-list">
    <li><svg width="10" height="14" viewBox="0 0 10 14"><path fill="#fff" d="M5 0a5 5 0 0 0-5 5c0 4 5 9 5 9s5-5 5-9a5 5 0 0 0-5-5zm0 7a2 2 0 1 1 0-4 2 2 0 0 1 0 4z"/></svg><span>118 Foundry Lane<br>Marlow, IL 60512</span></li>
    <li><svg width="12" height="12" viewBox="0 0 24 24"><path fill="#fff" d="M6.6 10.8a15 15 0 0 0 6.6 6.6l2.2-2.2c.3-.3.7-.4 1-.2 1.1.4 2.3.6 3.6.6.6 0 1 .4 1 1V20c0 .6-.4 1-1 1A17 17 0 0 1 3 4c0-.6.4-1 1-1h3.5c.6 0 1 .4 1 1 0 1.3.2 2.5.6 3.6.1.3 0 .7-.2 1z"/></svg><span>555.010.4477</span></li>
    <li><svg width="13" height="10" viewBox="0 0 13 10"><rect width="13" height="10" fill="#fff"/><path d="M0 0l6.5 5L13 0" stroke="#5a2787" fill="none"/></svg><span>hello@k7electric.com</span></li>
  </ul>
</div>
<div class="footer-col abs" style="left:688px">
  <h5>MENU</h5>
  <ul><li>Home</li><li>About Us</li><li>Services</li><li>Testimonials</li><li>Blog</li><li>Contact Us</li></ul>
</div>
<div class="footer-col abs" style="left:861px">
  <h5>NEWSLETTER</h5>
  <div class="email-field">E mail id</div>
  <div class="signup">SIGNUP</div>
</div>
<div class="footer-rule abs"></div>
<div class="footer-follow abs"><span class="label">FOLLOW US</span><span class="dot"></span><span class="dot"></span><span class="dot"></span></div>
<div class="copyright abs">Copyrights @ 2018 All Rights Reserved</div>

</body>
</html>
```